Bench Advertisement - We Buy Houses Design Needed

Need a catchy, simple but elegant design for bus benches to advertise our company.

We need our website, or phone number, and a smal description (1-2 bulletpoints of what we do and what we offer)

The tricky part is for the designer to fit everything and make the website name as part of the title and fitting everything so that people passing by on the street can see what we offer.

Our website is quickdealhomebuyer.com - (916) 555-0143

Something simple but something that catches the eye of walking pedestrians, and drivers driving by the bench.

Our company buys houses, any condition, any situation, we buy houses for cash and close quickly. You can use this description to create a few bulletpoints however you like. Must follow dimensions in attachment.

Target Market(s)

People in foreclosure, about to lose their homes, people that need a quick cash sale of their property

Industry/Entity Type

Real Estate

Requirements
Must have
• catchy, website name, phone number, few brief bulletpoints about what we offer, colors that will catch peoples eye while walking or driving - advertisement will be placed on bus benches - visit our website to see the type of houses we buy - Also have more work for winner of design with possible bonuses
Nice to have
• Feel free to use description or images on our website - make sure the description is just bullet points and it fits with the overall theme / size of the advertisement - Bold bright colors - put yourself in their shoes (if you were going through financial difficulties and about to lose your house to foreclosure or auction, what would you want to see to pick up the phone and call us for a quick sale of your house?) (or if you have a house that you are having a problem with, problem renters, unkept/beat up house, what would make you want to call us and sell your house to us?)

```html
<!DOCTYPE html>
<html lang="en">
<head>
<meta charset="utf-8">
<title>Quick Deal Home Buyer – Bench Advertisement</title>
<link href="https://fonts.googleapis.com/css2?family=Open+Sans:wght@400;600&family=PT+Sans+Narrow:wght@700&display=swap" rel="stylesheet">
<style>
  :root {
    --backdrop: #2b2b2b;
    --teal-light: #6db5c1;
    --teal-dark: #3a8597;
    --teal-text: #3b8a9b;
    --accent-orange: #f08a2c;
    --white: #ffffff;
    --caption-grey: #7a7a7a;
  }
  * { margin: 0; padding: 0; box-sizing: border-box; }
  html, body {
    width: 1200px; height: 768px; overflow: hidden;
    background: var(--backdrop);
  }
  .bench-ad {
    position: absolute; left: 40px; top: 228px;
    width: 1120px; height: 311px;
    background: var(--white);
    font-family: "Open Sans", Arial, sans-serif;
  }
  .ad-header {
    position: absolute; left: 0; top: 0; width: 100%; height: 182px;
    background: linear-gradient(to bottom, var(--teal-light), var(--teal-dark));
    border-bottom: 3px solid var(--accent-orange);
  }
  .brand-name {
    position: absolute; left: 38px; top: 108px;
    color: var(--white); font-weight: 400; font-size: 21px;
    letter-spacing: 0.2px; white-space: nowrap;
  }
  .contact {
    position: absolute; right: 42px; top: 22px;
    text-align: right; color: var(--white); font-weight: 600;
    line-height: 1;
  }
  .contact .phone { font-size: 44px; }
  .contact .website { font-size: 33px; margin-top: 8px; font-weight: 400; }
  .contact .tagline { font-size: 38px; margin-top: 9px; }
  .offer-list {
    position: absolute; left: 36px; top: 212px; list-style: none;
    font-family: "PT Sans Narrow", "Arial Narrow", sans-serif;
    font-weight: 700; font-size: 24px; color: var(--teal-text);
    line-height: 31px;
  }
  .offer-list li { display: flex; align-items: center; gap: 10px; }
  .offer-list li::before {
    content: ""; width: 14px; height: 14px; flex: none;
    background:
      linear-gradient(var(--teal-text), var(--teal-text)) 0 0 / 6px 6px no-repeat,
      linear-gradient(var(--teal-text), var(--teal-text)) 8px 0 / 6px 6px no-repeat,
      linear-gradient(var(--teal-text), var(--teal-text)) 0 8px / 6px 6px no-repeat,
      linear-gradient(var(--teal-text), var(--teal-text)) 8px 8px / 6px 6px no-repeat;
  }
  .steps {
    position: absolute; top: 212px; left: 0; width: 100%; height: 80px;
  }
  .step {
    position: absolute; width: 110px; margin-left: -55px;
    text-align: center;
  }
  .step svg { display: block; margin: 0 auto; }
  .step p {
    margin-top: 4px; font-size: 8px; line-height: 9px;
    color: var(--caption-grey); text-transform: uppercase;
  }
</style>
</head>
<body>
<div class="bench-ad">
  <header class="ad-header">
    <div class="brand-name">QUICK DEAL HOME BUYER</div>
    <div class="contact">
      <div class="phone">Cell (916) 555-0143</div>
      <div class="website">QUICKDEALHOMEBUYER.COM</div>
      <div class="tagline">WE MAKE IT SIMPLE</div>
    </div>
  </header>

  <ul class="offer-list">
    <li>OUR COMPANY BUYS HOUSES, ANY CONDITION, ANY SITUATION</li>
    <li>WE BUY HOUSES FOR CASH &amp; CLOSE QUICKLY</li>
  </ul>

  <div class="steps">
    <div class="step" style="left:672px">
      <svg width="46" height="46" viewBox="0 0 46 46" aria-hidden="true">
        <circle cx="23" cy="23" r="23" fill="var(--teal-dark)"/>
        <rect x="15" y="14" width="14" height="18" rx="1" fill="none" stroke="#fff" stroke-width="1.6"/>
        <path d="M18 19h8M18 23h8M18 27h5" stroke="#fff" stroke-width="1.4"/>
        <path d="M26 30l6-7" stroke="#fff" stroke-width="2"/>
      </svg>
      <p>Fill out the form</p>
    </div>
    <div class="step" style="left:794px">
      <svg width="46" height="46" viewBox="0 0 46 46" aria-hidden="true">
        <circle cx="23" cy="23" r="23" fill="var(--teal-dark)"/>
        <path d="M16 15c-2 2-1 7 4 12s10 6 12 4l1-2-4-3-2 2c-2-1-5-4-6-6l2-2-3-4z" fill="#fff"/>
        <path d="M25 14l5 0 0 5M30 14l-6 6" stroke="#fff" stroke-width="1.6" fill="none"/>
      </svg>
      <p>We'll call you within a few hours</p>
    </div>
    <div class="step" style="left:915px">
      <svg width="46" height="46" viewBox="0 0 46 46" aria-hidden="true">
        <circle cx="23" cy="23" r="23" fill="var(--teal-dark)"/>
        <rect x="14" y="21" width="4" height="10" fill="none" stroke="#fff" stroke-width="1.5"/>
        <path d="M18 22l4-7c2 0 3 1 2 5h6c1 0 2 1 1 2l-2 8c0 1-1 1-2 1h-9z" fill="none" stroke="#fff" stroke-width="1.5" stroke-linejoin="round"/>
      </svg>
      <p>We work with you on a solution</p>
    </div>
    <div class="step" style="left:1037px">
      <svg width="46" height="46" viewBox="0 0 46 46" aria-hidden="true">
        <circle cx="23" cy="23" r="23" fill="var(--teal-dark)"/>
        <path d="M13 24l10-9 10 9h-3v8h-5v-5h-4v5h-5v-8z" fill="#fff"/>
      </svg>
      <p>Move on with your life</p>
    </div>
  </div>
</div>
</body>
</html>
```